Spa brochure design

I need a brochure for my day spa boutique
Updates

Here is a new and approved services I do I took it from my website....

Velvet Bloom Signature Facials are customized for all skin types, they include steam, cleanse, tone, exfoliate, extractions, massage of neck, shoulders, head, hands and arms, masque, serum, moisturizer and sun protect...your skin will be radiant, healthy and glowing.  You will instantly notice the difference in the overall tone and texture of your skin. (60 mins) add on a Micro Dermabrasion, Peel or both.  Treatments and Services we provide are:

 

Velvet Bloom Facials 

Velvet Bloom Signature Facials:

Our Signature Facial is 60 minutes of pure heaven for only $60.00  - add on a Micro Dermabrasion, a Peel or both for just $30.00 each.

Velvet Bloom Oxygen Facials:

The Oxygen Facial can give you a detoxifying facial which is excellent for clearing pollutants and toxins from the skin thus improving cell function and increasing oxygen intake it achieve complete, immediate and visible results absolutely perfect for those who have an event to go to. Deep lines and visible wrinkles fade with regular treatment. (75 min) $130.00 

Velvet Bloom Oxygen Micro Facial:

This treatment can give you a detoxifying Oxygen Facial which is excellent for clearing pollutants and toxins from the skin thus improving cell function and increasing oxygen intake. It combines the healing effects of oxygen and serum into one treatment by boosting oxygen levels, the result is a younger, fresher looking skin this plus regular stimulation and micro-circulation of needed exfoliation aids in the production of new collagen and elastinformulation and achieve complete, immediate and visible results deep lines and visible wrinkles fade with regular treatment. $175.00  

Velvet Bloom Back Facial:

A soothing and relaxing treatment for the back especially helps with breakouts and gets rid of impurities where you can't always reach includes cleanse, tone, steam, exfoliate, extractions, masque, moisturizer and sun protection. (45 min) $45.00

Facial on the Rocks:

A Velvet Bloom Signature Facial with added warm stones that makes it that much more relaxing.
(60 min)  $95.00

Teen or On the Go Facial:

Cleansing of the skin, steam, extractions, masque, moisturizer, sun protection (30 min) $45.00

 Add on to any Facial Enzyme Treatment or Specialty Masque $10.00 

Microdermabrasion & Facial Peels

Renewal Microdermabrasion Facial:

A beautiful anti aging treatment that is a exfoliating and resurfacing treatment geared towards those with hyper-pigmentation, fine lines and wrinkles includes: A customized facial for all skin types also face, neck and shoulder massage. (70 min)  $90.00

Renewal Microdermabrasion Treatment:

exfoliating treatment that is a resurfacing treatment, perfect for those with larger pores, hyper-pigmentation,fine lines, and wrinkles also helps with elasticity includes: cleansing, a masque, moisturizer, and sun protection.
(30 min) $60.00

Rejuvenate Glycolic Acid Peel Treatment:

Perfect for normal to dry skin types intensive but safe treatment designed to rapidly exfoliate skin cells, reduces appearance of fine lines, wrinkles and sun damage includes: cleansing, masque, moisturizer, and sun protection. (30 min)  $55.00

Rejuvenate Salicylic Acid Peel Treatment:

Great for oily or acne skin types. This peel exfoliates the pores to allow natural oil production and helps to get sebum production under control includes: cleansing, masque, moisturizer and sun protection. (30 min)  $55.00

Velvet Bloom Massage

Swedish Massage (60 min, 70 min and 90 min)
Aromatherapy Massage $75.00
Deep Tissue Massage $80.00
Pregnancy Massage $70.00
Massage on the Rocks $90.00

Stress Relief Treatment:

A Deep Massage of the Neck, Shoulders and Scalp (15 min) $15.00 (add on to any facial for a $1.00 a minute)

Happy Feet:

Massage and Reflexology of your tired feet (30 min) $30.00  

Waxing Services

Eye Brow Shaping and Trimming  $15.00
Eye Brow Clean-Up $10.00
Lip or Chin $10.00
Face Wax (lip/brow shaping/ chin) $30.00
Side Burns $15.00
Arm Wax:  1/2 arm $25.00 Full are $50.00
Under Arm $25.00
Bikini Wax Starting at $30.00+
Legs 1/2 $30.00+ Full legs $50+
Back Wax $50+

Nail Treatments

Manicure
Pedicure
Foot Detox
Silk Wrap
Hand and Foot Massage and Mask Treatment
Gel Nail 
Polivance Frenchie Manicure $40.00
Polivance Manicure  $35.00
Polivance Pedicure $50.00
Polivance Frenchie Pedicure $60.00
Manicure on the Rocks

Add to any Nail Service:  Polivance $10.00Frenchie $6.00, Hand polish change $8.00, Cut down $2.00, Toe polish change $12.00, One nail repair $5.00, Paraffin Hand Treatment $10.00Foot Treatment $15.00

Eye Lash Treatments

Eye Lash Tinting:

Make your own lashes stand out  "No more fake lashes and glue stuck to your eyes" (30 min) $30.00

Eye Brow Tinting:

Make your brows look Perfect 'No more penciling them in" (30 min) $20.00

For Both Eye Lash and Eye Brow Tinting:

$40.00

Here's my packages....

Velvet Bloom Signature Facials are customized for all skin types, they include steam, cleanse,tone, exfoliate, extractions, massage of neck, shoulders, head, hands and arms, masque, serum, moisturizer and sun protect...your skin will be radiant, healthy and glowing.  You'll instantly notice the difference in the overall tone and texture of you skin. (60 mins) add on a Microdermabrasion, Peel, or both.  Book in for one of beautiful Treatment Packages or Purchase a Treatment Package below as a gift, our treatments include:

Nora Whitfield Package:

Our 75 minute Swedish Massage combined with both a hand paraffin treatment and a foot detox treatment for a revitalizing experience valued at $225.00 now only $125.00.

Clara Delmont Package:

Enjoy a Luxury Spa Manicure then a Spa Pedicure at the same time, as a Larkspur Botanic Signature Facial that will stimulate all your senses head to toe, and a Stress relief Treatment our regular price is valued at $220.00 now only $170.00.

Ruby Ashcombe Package:

Our ultimate Relaxing Pearl Haze Package is our  favorite treatment combined together into one Package includes an Oxygen Facial,  Spa Manicure, Pedicure, and a 60 minute Swedish Massage is valued at $300.00 now only $210.00.

Industry/Entity Type

Boutique

Font styles to use
Serif
Decorative
Script

Requirements
Must have
• My spa and boutiques service,prices, products we use and retail, logo,and have purple and white for colors on brochure.

```html
<!DOCTYPE html>
<html lang="en">
<head>
<meta charset="utf-8">
<title>Velvet Bloom Spa Brochure</title>
<link rel="stylesheet" href="https://fonts.googleapis.com/css2?family=Arimo:ital,wght@0,400;0,700;1,700&family=Fira+Sans:wght@500;600&display=swap">
<style>
  :root {
    --purple: #8a63b0;
    --purple-line: #9575bd;
    --ink: #3a3a3a;
    --muted: #9a9a9a;
    --white: #ffffff;
    --backdrop: #e4e4e4;
  }
  * { box-sizing: border-box; margin: 0; padding: 0; }
  html, body { width: 1200px; height: 900px; overflow: hidden; background: var(--backdrop); }
  .canvas { position: relative; width: 1200px; height: 900px; }
  .brochure {
    position: absolute; left: 173px; top: 153px; width: 842px; height: 598px;
    background: var(--white); overflow: hidden;
    font-family: "Arimo", Arial, sans-serif; color: var(--ink);
  }
  .abs { position: absolute; }

  /* backgrounds and photos */
  .spa-still-life {
    left: 0; top: 270px; width: 764px; height: 328px;
    background:
      linear-gradient(180deg, rgba(255,255,255,1) 0%, rgba(255,255,255,0) 45%),
      linear-gradient(100deg, #d8cde6 0%, #ece8e3 35%, #cdc6bc 70%, #e8e1cf 100%);
  }
  .panel-white { background: var(--white); }
  .panel-services { left: 295px; top: 0; width: 252px; height: 550px; }
  .panel-peels { left: 575px; top: 0; width: 267px; height: 547px; }
  .round-photo {
    width: 166px; height: 166px; border-radius: 50%;
    border: 5px solid var(--white);
    box-shadow: 0 3px 8px rgba(0,0,0,0.35);
    background: linear-gradient(150deg, #f4e2d6 0%, #e2bfa8 55%, #b99585 100%);
  }
  .photo-facial-mask { left: 339px; top: -85px; }
  .photo-facial-tool { left: 617px; top: -88px; }
  .photo-massage {
    left: 745px; top: 387px; width: 76px; height: 58px; border-radius: 30px 0 0 30px;
    background: linear-gradient(120deg, #f7e5d8 0%, #e0b79c 60%, #c79a80 100%);
  }

  /* left panel */
  .gift-line { left: 0; width: 284px; top: 32px; text-align: center; font-size: 9px; font-weight: 700; color: #111; }
  .packages-title {
    left: 0; width: 284px; top: 54px; text-align: center;
    font-family: "Fira Sans", Arial, sans-serif; font-weight: 600; font-size: 15px; color: var(--purple); letter-spacing: 0.2px;
  }
  .package-card {
    left: 53px; width: 177px; height: 104px;
    border: 3px solid var(--purple-line); background: var(--white);
    padding: 21px 13px 0 14px;
  }
  .package-card h3 { font-size: 9.5px; color: var(--purple); font-weight: 700; margin-bottom: 4px; }
  .package-card p { font-size: 8px; line-height: 9.6px; font-weight: 700; text-align: justify; color: var(--ink); }
  .card-nora { top: 115px; }
  .card-clara { top: 265px; }
  .card-ruby { top: 420px; }
  .portrait {
    width: 52px; height: 52px; border-radius: 50%;
    border: 2px solid var(--purple-line); background: var(--white); padding: 3px;
  }
  .portrait span { display: block; width: 100%; height: 100%; border-radius: 50%;
    background: linear-gradient(160deg, #d4d4d4 0%, #8a8a8a 100%); }
  .portrait-nora { left: 116px; top: 84px; }
  .portrait-clara { left: 116px; top: 229px; }
  .portrait-ruby { left: 116px; top: 382px; }

  /* service columns */
  .column { width: 234px; }
  .col-services { left: 304px; }
  .col-peels { left: 584px; }
  .section-title { font-family: "Fira Sans", Arial, sans-serif; font-weight: 600; font-size: 12.5px; color: var(--purple); }
  .intro { font-size: 7px; line-height: 8.3px; font-style: italic; font-weight: 700; color: var(--muted); text-align: justify; letter-spacing: -0.05px; }
  .item-title { font-size: 10px; font-weight: 700; color: var(--purple); }
  .item-body { font-size: 7px; line-height: 8.6px; font-weight: 700; color: var(--ink); text-align: justify; letter-spacing: -0.1px; }
  .price { color: var(--purple); }
  .rule { height: 1px; background: var(--purple-line); }
  .massage-list { font-size: 7px; line-height: 9.4px; font-weight: 700; color: var(--ink); list-style: none; }
</style>
</head>
<body>
<div class="canvas">
  <div class="brochure">
    <div class="abs spa-still-life" role="img" aria-label="Spa still life with rolled white towels, purple iris flowers, stacked basalt stones and a candle"></div>
    <div class="abs panel-white panel-services"></div>
    <div class="abs panel-white panel-peels"></div>

    <div class="abs round-photo photo-facial-mask" role="img" aria-label="Photo of a woman receiving a facial mask with a brush"></div>
    <div class="abs round-photo photo-facial-tool" role="img" aria-label="Photo of a woman receiving a microdermabrasion facial"></div>

    <!-- Packages panel -->
    <p class="abs gift-line">Gift Card and Packages Available</p>
    <h2 class="abs packages-title">TREATMENT PACKAGES</h2>

    <div class="abs package-card card-nora">
      <h3>Nora Whitfield Package</h3>
      <p>Our 75 minute Swedish Massage combined with both a hand paraffin treatment and a foot detox treatment for a revitalizing experience now only <span class="price">$125.00.</span></p>
    </div>
    <div class="abs portrait portrait-nora" role="img" aria-label="Vintage portrait"><span></span></div>

    <div class="abs package-card card-clara">
      <h3>Clara Delmont Package</h3>
      <p>Enjoy a Luxury Spa Manicure then a Spa Pedicure at the same time, as a Larkspur Botanic Signature Facial that will stimulate all your senses head to toe, and a Stress relief Treatment <span class="price">$170.00.</span></p>
    </div>
    <div class="abs portrait portrait-clara" role="img" aria-label="Vintage portrait"><span></span></div>

    <div class="abs package-card card-ruby">
      <h3>Ruby Ashcombe Package</h3>
      <p>Our ultimate Relaxing Pearl Haze Package is are favorite treatments combined together into one Package a Oxygen Facial, Spa Manicure, Pedicure, and a 60 min. Swedish Massage.$300 value for <span class="price">$210.00.</span></p>
    </div>
    <div class="abs portrait portrait-ruby" role="img" aria-label="Vintage portrait"><span></span></div>

    <!-- Services column -->
    <h2 class="abs section-title col-services" style="top:106px;">OUR SERVICE</h2>
    <p class="abs intro column col-services" style="top:128px;">Velvet Bloom Signature Facials are customized for all skin types, they include steam, cleanse, tone, exfoliate, extractions, massage of neck, shoulders, head, hands and arms, masque, serum, moisturizer and sun protect...your skin will be radiant, healthy and glowing. You will instantly notice the difference in the overall tone and texture of your skin. (60 mins) add on a Micro Dermabrasion, Peel or both.</p>
    <h2 class="abs section-title col-services" style="top:187px;">Velvet Bloom Facials</h2>

    <h3 class="abs item-title col-services" style="top:218px;">Velvet Bloom Signature Facials:</h3>
    <p class="abs item-body column col-services" style="top:235px;">Our Signature Facial is 60 minutes of pure heaven for only <span class="price">$60.00</span> add on a Micro Dermabrasion, a Peel or both for just <span class="price">$30.00</span> each.</p>
    <div class="abs rule column col-services" style="top:260px;"></div>

    <h3 class="abs item-title col-services" style="top:268px;">Velvet Bloom Oxygen Facials:</h3>
    <p class="abs item-body column col-services" style="top:284px;">The Oxygen Facial can give you a detoxifying facial which is excellent for clearing pollutants and toxins from the skin thus improving cell function and increasing oxygen intake it achieve complete, immediate and visible results absolutely perfect for those who have an event to go to. Deep lines and visible wrinkles fade with regular treatment. (75 min) <span class="price">$130.00</span></p>
    <div class="abs rule column col-services" style="top:342px;"></div>

    <h3 class="abs item-title col-services" style="top:351px;">Velvet Bloom Back Facial:</h3>
    <p class="abs item-body column col-services" style="top:368px;">A soothing and relaxing treatment for the back especially helps with breakouts and gets rid of impurities where you can't always reach includes cleanse, tone, steam, exfoliate, extractions, masque, moisturizer and sun protection. (45 min) <span class="price">$45.00.</span></p>
    <div class="abs rule column col-services" style="top:411px;"></div>

    <h3 class="abs item-title col-services" style="top:420px;">Facial on the Rocks:</h3>
    <p class="abs item-body column col-services" style="top:437px;">A soothing and relaxing treatment for the back especially helps with A Velvet Bloom Signature Facial with added warm stones that makes it that much more relaxing. (60 min) <span class="price">$95.00.</span></p>
    <div class="abs rule column col-services" style="top:471px;"></div>

    <h3 class="abs item-title col-services" style="top:479px;">Teen or On the Go Facial:</h3>
    <p class="abs item-body column col-services" style="top:496px;">Cleansing of the skin, steam, extractions, masque, moisturizer, sun protection (30 min) <span class="price">$45.00</span></p>
    <p class="abs item-body column col-services" style="top:521px;">Add on to any Facial Enzyme Treatment or Specialty Masque <span class="price">$10.00.</span></p>

    <!-- Peels and massage column -->
    <h2 class="abs section-title col-peels" style="top:105px;">Microdermabrasion &amp; Facial Peels</h2>

    <h3 class="abs item-title col-peels" style="top:127px;">Renewal Microdermabrasion Facial:</h3>
    <p class="abs item-body column col-peels" style="top:143px;">A beautiful anti aging treatment that is a exfoliating and resurfacing treatment geared towards those with hyper-pigmentation, fine lines and wrinkles includes: A customized facial for all skin types also face, neck and shoulder massage. (70 min) <span class="price">$90.00</span></p>
    <div class="abs rule column col-peels" style="top:186px;"></div>

    <h3 class="abs item-title col-peels" style="top:195px;">Renewal Microdermabrasion Treatment:</h3>
    <p class="abs item-body column col-peels" style="top:212px;">A exfoliating treatment that is a resurfacing treatment, perfect for those with larger pores, hyper-pigmentation,fine lines, and wrinkles also helps with elasticity includes: cleansing, a masque, moisturizer, and sun protection (30 min) <span class="price">$60.00</span></p>
    <div class="abs rule column col-peels" style="top:253px;"></div>

    <h3 class="abs item-title col-peels" style="top:261px;">Rejuvenate Glycolic Acid Peel Treatment:</h3>
    <p class="abs item-body column col-peels" style="top:277px;">Perfect for normal to dry skin types intensive but safe treatment designed to rapidly exfoliate skin cells, reduces appearance of fine lines, wrinkles and sun damage includes: cleansing, a masque, moisturizer, and sun protection. (30 min) <span class="price">$55.00</span></p>
    <div class="abs rule column col-peels" style="top:315px;"></div>

    <h3 class="abs item-title col-peels" style="top:323px;">Rejuvenate Salicylic Acid Peel Treatment:</h3>
    <p class="abs item-body column col-peels" style="top:340px;">Great for oily or acne skin types. This peel exfoliates the pores to allow natural oil production and helps to get sebum production under control includes: cleansing, masque, moisturizer and sun protection. (30 min) <span class="price">$55.00.</span></p>
    <div class="abs rule column col-peels" style="top:380px;"></div>

    <h3 class="abs item-title col-peels" style="top:387px;">Velvet Bloom Massage</h3>
    <div class="abs photo-massage" role="img" aria-label="Photo of a woman relaxing during a massage"></div>
    <ul class="abs massage-list col-peels" style="top:404px;">
      <li>Swedish Massage (60 min, 70 min and 90 min)</li>
      <li>Aromatherapy Massage <span class="price">$75.00</span></li>
      <li>Deep Tissue Massage <span class="price">$80.00</span></li>
      <li>Pregnancy Massage <span class="price">$70.00</span></li>
      <li>Massage on the Rocks <span class="price">$90.00</span></li>
    </ul>
    <div class="abs rule column col-peels" style="top:452px;"></div>

    <h3 class="abs item-title col-peels" style="top:461px;">Stress Relief Treatment:</h3>
    <p class="abs item-body column col-peels" style="top:478px;">A Deep Massage of the Neck, Shoulders and Scalp (15 min) <span class="price">$15.00</span><br>(add on to any facial for a <span class="price">$1.00</span> a minute)</p>
    <div class="abs rule column col-peels" style="top:500px;"></div>

    <h3 class="abs item-title col-peels" style="top:505px;">Happy Feet:</h3>
    <p class="abs item-body column col-peels" style="top:521px;">Massage and Reflexology of your tired feet (30 min) <span class="price">$30.00</span></p>
  </div>
</div>
</body>
</html>
```